Stationery Design Project for Nimbora, Chicago

Nimbora, a street parking application which helps car drivers find a street parking spot by offering an ideal path along which to look for parking. This path is calculated by our algorithm based on data (e.g. historical data, baseball games schedule, etc.). Along this path the driver will find a spot and will also save 70% of the search time. Customer we target is reg. between 21 and 45 yo.

We envision something young, fresh, bright and original. Slightly abstract maybe. It should represent the idea and elements of finding street parking in the city, e.g. car(s), parking spot, people, city, etc. (just ideas!).

Logo is attached.

Requirement:
- Business Cards (2 Sided Full Color CMYK)
- Letterhead (1 Sided Full Color CMYK)
- Envelope (1 Sided Full Color CMYK)
- Sticker (1 Sided Full Color CMYK), round with a 2inch diameter.

Reason: We're starting to get more and more designs and need more time to look into all of them. Very exciting!! Thanks to everybody!

Hi all, we're in the process of selecting our favs. Though choices!!! Really good submissions. Will keep you posted and sorry for the delay.

Target Market(s)

Car drivers and owners between 21 and 45

Industry/Entity Type

Parking

Requirements
Must have
• Sticker should be round and include company URL nimbora.com and the new logo which we will attach soon.
Should not have
• Should not be too serious or boring.

```html
<!DOCTYPE html>
<html lang="en">
<head>
<meta charset="utf-8">
<title>Nimbora Business Card</title>
<link rel="stylesheet" href="https://fonts.googleapis.com/css2?family=Open+Sans:wght@400;600;700&display=swap">
<style>
  :root {
    --page: #ecebe8;
    --card: #ffffff;
    --brand-blue: #1f7bc1;
    --ink: #2a2a2a;
    --muted: #6b6b6b;
    --url-grey: #555555;
  }
  * { margin: 0; padding: 0; box-sizing: border-box; }
  html, body { width: 1200px; height: 758px; overflow: hidden; }
  body {
    background: var(--page);
    font-family: "Open Sans", Arial, sans-serif;
    position: relative;
  }
  .card {
    position: absolute;
    width: 520px;
    height: 300px;
    background: var(--card);
    border-radius: 30px;
    box-shadow: 0 6px 18px rgba(0,0,0,0.18);
    overflow: hidden;
  }
  .card--front { left: 50px; top: 229px; }
  .card--back { left: 630px; top: 229px; }

  /* Front */
  .brand {
    position: absolute;
    left: 34px; top: 124px;
    display: flex; align-items: center; gap: 12px;
  }
  .brand__dot {
    width: 46px; height: 46px; border-radius: 50%;
    background: var(--brand-blue);
  }
  .brand__name {
    font-weight: 700; font-size: 34px; color: var(--ink);
    letter-spacing: -0.5px;
  }
  .band {
    position: absolute;
    left: 268px; top: 0;
    width: 24px; height: 100%;
    background: var(--brand-blue);
  }
  .band__url {
    position: absolute;
    left: 50%; top: 50%;
    transform: translate(-50%, -50%) rotate(-90deg);
    color: #fff; font-size: 13px; letter-spacing: 1px; white-space: nowrap;
  }
  .contact {
    position: absolute;
    left: 318px; top: 72px;
    color: var(--muted); font-size: 14px; line-height: 1.35;
  }
  .contact__name { color: var(--brand-blue); font-weight: 700; font-size: 18px; }
  .contact__title { margin-bottom: 12px; }
  .contact__line { display: flex; align-items: center; gap: 6px; }
  .contact__line svg { width: 11px; height: 11px; fill: var(--muted); flex: none; }
  .contact__address { margin-top: 14px; }

  /* Back */
  .mark {
    position: absolute;
    left: 0; right: 0; top: 62px;
    display: flex; align-items: center; justify-content: center; gap: 16px;
  }
  .mark__dot {
    width: 96px; height: 96px; border-radius: 50%;
    background: var(--brand-blue);
  }
  .mark__name { font-weight: 700; font-size: 40px; color: var(--ink); }
  .back__url {
    position: absolute;
    left: 0; right: 0; top: 214px;
    text-align: center;
    font-weight: 700; font-size: 26px; letter-spacing: 4px;
    color: var(--url-grey);
  }
</style>
</head>
<body>
  <section class="card card--front">
    <div class="brand">
      <div class="brand__dot"></div>
      <span class="brand__name">nimbora</span>
    </div>
    <div class="band"><span class="band__url">www.nimbora.com</span></div>
    <div class="contact">
      <div class="contact__name">Your Name</div>
      <div class="contact__title">Title</div>
      <div class="contact__line">
        <svg viewBox="0 0 12 12"><path d="M3 1l2 2-1 1.5c.7 1.5 1.8 2.6 3.5 3.5L9 7l2 2-1.5 2C5 10.5 1.5 7 1 2.5z"/></svg>
        123-456-789
      </div>
      <div class="contact__line">
        <svg viewBox="0 0 12 12"><rect x="3" y="0.5" width="6" height="11" rx="1"/><rect x="4" y="2" width="4" height="6" fill="#fff"/></svg>
        123-456-789
      </div>
      <div class="contact__line">
        <svg viewBox="0 0 12 12"><rect x="0.5" y="2.5" width="11" height="7"/><path d="M0.5 2.5L6 7l5.5-4.5" stroke="#fff" fill="none"/></svg>
        info@nimbora.com
      </div>
      <div class="contact__address">Complex name, Street name<br>City, State, zip code</div>
    </div>
  </section>

  <section class="card card--back">
    <div class="mark">
      <div class="mark__dot"></div>
      <span class="mark__name">nimbora</span>
    </div>
    <div class="back__url">www.nimbora.com</div>
  </section>
</body>
</html>
```